Dunmore Roofing

Want a professional looking business card

Industry/Entity Type

Business

Contact Information for Business Card

Paul Dunmore ( Owner) paul@dunmoreroofing-example.com, www.dunmoreroofing-example.com, Adress: 4172 Township road 43 Maplecrest,ON K9X4T2

```html
<!DOCTYPE html>
<html lang="en">
<head>
<meta charset="utf-8">
<title>Dunmore Roofing – Business Card</title>
<link href="https://fonts.googleapis.com/css2?family=Roboto:wght@400;500;700&display=swap" rel="stylesheet">
<style>
  :root {
    --brand-blue: #1b4589;
    --brand-grey: #6f6f6f;
    --text-grey: #6a6a6a;
    --card-white: #ffffff;
    --backdrop: #e6e6e6;
  }
  * { margin: 0; padding: 0; box-sizing: border-box; }
  html, body { width: 1200px; height: 1000px; overflow: hidden; }
  body {
    background: var(--backdrop);
    font-family: "Roboto", Arial, sans-serif;
    position: relative;
  }
  .card {
    position: absolute;
    left: 269px;
    width: 662px;
    height: 378px;
    overflow: hidden;
    box-shadow: 0 3px 6px rgba(0,0,0,0.25);
  }
  .card-front { top: 108px; background: var(--brand-blue); }
  .card-back { top: 521px; background: var(--card-white); }

  .wordmark { position: absolute; text-align: right; font-weight: 700; text-transform: uppercase; line-height: 1; }
  .wordmark .name-line { display: block; }
  .front-wordmark { right: 31px; top: 294px; color: var(--card-white); }
  .front-wordmark .name-line:first-child { font-size: 40px; letter-spacing: 1px; }
  .front-wordmark .name-line:last-child { font-size: 17px; letter-spacing: 18.5px; margin-top: 5px; margin-right: -17px; }

  .back-wordmark { right: 37px; top: 104px; color: var(--brand-blue); }
  .back-wordmark .name-line:first-child { font-size: 30px; letter-spacing: 1px; }
  .back-wordmark .name-line:last-child { font-size: 13px; letter-spacing: 13.5px; margin-top: 4px; margin-right: -13px; }
  .brand-square { position: absolute; right: 82px; top: 40px; width: 44px; height: 44px; background: var(--brand-blue); }

  .name-tab { position: absolute; left: 0; top: 185px; width: 8px; height: 34px; background: var(--brand-blue); }
  .person-name { position: absolute; left: 38px; top: 183px; font-size: 20px; font-weight: 500; color: var(--brand-blue); }
  .person-role { position: absolute; left: 38px; top: 208px; font-size: 15px; color: var(--text-grey); }

  .contact-list { position: absolute; left: 38px; top: 246px; list-style: none; font-size: 15px; color: var(--text-grey); }
  .contact-list li { display: flex; align-items: center; height: 21px; white-space: nowrap; }
  .contact-list li.address { margin-bottom: 11px; }
  .contact-list svg { width: 11px; height: 11px; margin-right: 6px; fill: var(--brand-blue); flex-shrink: 0; }
  .contact-list .accent { color: var(--brand-blue); }

  .footer-band { position: absolute; left: 0; bottom: 0; width: 662px; height: 12px; }
</style>
</head>
<body>
  <section class="card card-front" aria-label="Card front">
    <div class="wordmark front-wordmark">
      <span class="name-line">Dunmore</span>
      <span class="name-line">Roofing</span>
    </div>
  </section>

  <section class="card card-back" aria-label="Card back">
    <div class="brand-square"></div>
    <div class="wordmark back-wordmark">
      <span class="name-line">Dunmore</span>
      <span class="name-line">Roofing</span>
    </div>

    <div class="name-tab"></div>
    <p class="person-name">Paul Dunmore</p>
    <p class="person-role">Owner</p>

    <ul class="contact-list">
      <li class="address">
        <svg viewBox="0 0 12 12"><path d="M6 0a4 4 0 0 0-4 4c0 3 4 8 4 8s4-5 4-8a4 4 0 0 0-4-4zm0 5.6A1.6 1.6 0 1 1 6 2.4a1.6 1.6 0 0 1 0 3.2z"/></svg>
        4172 Township road 43 Maplecrest, ON K9X4T2
      </li>
      <li>
        <svg viewBox="0 0 12 12"><path d="M2.4 0.6l2 2-1.1 1.6c.8 1.7 2.1 3 3.8 3.8l1.6-1.1 2 2-1.4 1.9C4.8 10.6 1.4 7.2.5 2z"/></svg>
        (613) 555-0142
      </li>
      <li>
        <svg viewBox="0 0 12 12"><path d="M0 2h12v8H0zM1 3l5 3.5L11 3v-.2H1z" fill-rule="evenodd"/></svg>
        paul@dunmoreroofing-example.com
      </li>
      <li>
        <svg viewBox="0 0 12 12"><path d="M6 0a6 6 0 1 0 0 12A6 6 0 0 0 6 0zm4.9 5.3H8.6a9 9 0 0 0-.8-3.6 5 5 0 0 1 3.1 3.6zM6 1c.6.8 1.2 2.3 1.3 4.3H4.7C4.8 3.3 5.4 1.8 6 1zM4.2 1.7a9 9 0 0 0-.8 3.6H1.1a5 5 0 0 1 3.1-3.6zM1.1 6.7h2.3a9 9 0 0 0 .8 3.6 5 5 0 0 1-3.1-3.6zM6 11c-.6-.8-1.2-2.3-1.3-4.3h2.6C7.2 8.7 6.6 10.2 6 11zm1.8-.7a9 9 0 0 0 .8-3.6h2.3a5 5 0 0 1-3.1 3.6z"/></svg>
        <span>www.<span class="accent">dunmoreroofing-example</span>.com</span>
      </li>
    </ul>

    <svg class="footer-band" viewBox="0 0 662 12" aria-hidden="true">
      <polygon points="0,4 330,4 326,12 0,12" fill="var(--brand-grey)"/>
      <polygon points="336,2 662,2 662,12 330,12" fill="var(--brand-blue)"/>
    </svg>
  </section>
</body>
</html>
```